Modern, clean business card for Clearbrook Optics

Updated business card with a modern look.

Logo on the front
Dr Tavin R Marquell and Associates on the front.
Three locations on the back:
Ridgefront Brantmart
509-555-0142
18342 E Fernhollow Ave

Pelham Brantmart
509-555-0187
4716 W Dunmore Ave

Copper Bluff Brantmart
509-555-0163
3854 S Kettering Rd

Facebook icon. www.clearbrookoptix.example

Nice open white space on back for writing next appointment time.

Target Market(s)

Main target is female 25-50, but I would like broad appeal.

Industry/Entity Type

Healthcare

Contact Information for Business Card

Modern look

Font styles to use
Serif

Requirements
Must have
• Logo and Dr Tavin R Marquell and Associates on front.
• 3 locations on back
• white space for noting next appointment

```html
<!DOCTYPE html>
<html lang="en">
<head>
<meta charset="utf-8">
<title>Clearbrook Optics – Business Card</title>
<link rel="stylesheet" href="https://fonts.googleapis.com/css2?family=Open+Sans:wdth,wght@75..100,300..800&display=swap">
<style>
  :root {
    --bg: #e9e9e9;
    --card: #ffffff;
    --navy: #1d3566;
    --blue: #1e6fb8;
    --grey-text: #555555;
    --rule: #5a6478;
    --divider: #d6d6d6;
  }
  * { margin: 0; padding: 0; box-sizing: border-box; }
  html, body {
    width: 1200px; height: 750px; overflow: hidden;
    background: var(--bg);
    font-family: "Open Sans", Arial, sans-serif;
  }
  .card {
    position: absolute;
    top: 228px;
    width: 461px; height: 262px;
    background: var(--card);
    box-shadow: 0 4px 10px rgba(0,0,0,0.18);
  }
  .card--front { left: 124px; }
  .card--back { left: 618px; }

  .brand { position: absolute; text-align: center; }
  .brand__name {
    font-size: 21px; font-weight: 700; color: var(--navy);
    letter-spacing: 0.2px; white-space: nowrap; line-height: 1;
  }
  .brand__tagline {
    margin-top: 6px;
    font-size: 10.5px; font-weight: 600; color: var(--navy);
    letter-spacing: 0.3px; line-height: 1;
  }
  .card--front .brand { left: 28px; width: 200px; top: 152px; }
  .card--back .brand { left: 128px; width: 200px; top: 106px; }

  .divider {
    position: absolute; left: 244px; top: 36px;
    width: 1px; height: 200px; background: var(--divider);
  }
  .social-square {
    position: absolute; left: 436px; top: 7px;
    width: 17px; height: 17px; background: var(--blue);
  }
  .contact { position: absolute; left: 261px; top: 34px; }
  .contact__practice {
    font-size: 15px; font-weight: 700; font-stretch: 75%;
    color: var(--navy); line-height: 1; margin-bottom: 10px;
    margin-left: 0;
  }
  .location { margin-bottom: 7px; }
  .location__name {
    font-size: 12.5px; font-weight: 600; color: var(--grey-text); line-height: 16px;
  }
  .location__line {
    font-size: 12px; font-weight: 400; color: var(--grey-text); line-height: 16px;
  }
  .contact__web {
    font-size: 12px; color: var(--grey-text); line-height: 16px; margin-left: 2px;
  }

  .appt { position: absolute; color: var(--navy); font-size: 13px; line-height: 1; }
  .appt__rule { position: absolute; height: 1px; background: var(--rule); }
</style>
</head>
<body>
  <section class="card card--front">
    <div class="brand">
      <div class="brand__name">Clearbrook Optics</div>
      <div class="brand__tagline">ADVANCED EYE CARE</div>
    </div>
    <div class="divider"></div>
    <div class="social-square" role="img" aria-label="Social page"></div>
    <div class="contact">
      <div class="contact__practice">Dr Tavin R Marquell &amp; Associates</div>
      <div class="location">
        <div class="location__name">Ridgefront Brantmart</div>
        <div class="location__line">509-555-0142</div>
        <div class="location__line">18342 E Fernhollow Ave</div>
      </div>
      <div class="location">
        <div class="location__name">Pelham Brantmart</div>
        <div class="location__line">509-555-0187</div>
        <div class="location__line">4716 W Dunmore Ave</div>
      </div>
      <div class="location">
        <div class="location__name">Copper Bluff Brantmart</div>
        <div class="location__line">509-555-0163</div>
        <div class="location__line">3854 S Kettering Rd</div>
      </div>
      <div class="contact__web">www.clearbrookoptix.example</div>
    </div>
  </section>

  <section class="card card--back">
    <div class="brand">
      <div class="brand__name">Clearbrook Optics</div>
      <div class="brand__tagline">ADVANCED EYE CARE</div>
    </div>
    <span class="appt" style="left:36px; top:182px;">Name</span>
    <div class="appt__rule" style="left:76px; top:194px; width:348px;"></div>
    <span class="appt" style="left:36px; top:219px;">Date</span>
    <div class="appt__rule" style="left:75px; top:231px; width:163px;"></div>
    <span class="appt" style="left:249px; top:219px;">Time</span>
    <div class="appt__rule" style="left:287px; top:231px; width:88px;"></div>
    <span class="appt" style="left:382px; top:219px;">am/pm</span>
  </section>
</body>
</html>
```